Company identity deisgn should support 2 languages

I would like to get our company identity design
This includes the following only
Business Cards 2 languages Arabic and English
Email signature
Letterhead
Linkedin profile images
Attached is the logo in Ai format

Requirements
Must have
• For business card
Must have
Name and Adrees in arabic
Name and Address in english
You might use both side of the card
Should not have
• Any pictures other than the logo

```html
<!DOCTYPE html>
<html lang="en">
<head>
<meta charset="utf-8">
<title>Lumen Systems – Business Card</title>
<link rel="stylesheet" href="https://fonts.googleapis.com/css2?family=Roboto:wght@400;500;700&family=Tajawal:wght@400;500;700&display=swap">
<style>
  :root {
    --page: #e9e8e6;
    --card: #f4f4f4;
    --blue: #1a6fc0;
    --grey: #5e6066;
    --text: #55575c;
    --faint: #dfe6ee;
  }
  * { box-sizing: border-box; margin: 0; padding: 0; }
  html, body { width: 1200px; height: 960px; overflow: hidden; }
  body {
    background: var(--page);
    font-family: "Roboto", Arial, sans-serif;
    display: flex;
    flex-direction: column;
    align-items: center;
    justify-content: center;
    gap: 40px;
  }
  .card {
    position: relative;
    width: 760px;
    height: 434px;
    background: var(--card);
    overflow: hidden;
    box-shadow: 0 4px 14px rgba(0,0,0,0.12);
  }
  .card__decor {
    position: absolute;
    right: 40px;
    top: 40px;
    width: 300px;
    height: 300px;
    border-radius: 50%;
    background: var(--faint);
  }
  .card__band {
    position: absolute;
    left: 0; right: 0; bottom: 0;
    height: 12px;
    display: flex;
  }
  .card__band-blue { flex: 0 0 58%; background: var(--blue); }
  .card__band-grey { flex: 1; background: var(--grey); }
  .brand {
    position: absolute;
    left: 64px;
    top: 96px;
    display: flex;
    align-items: center;
    gap: 14px;
  }
  .brand__dot {
    width: 34px; height: 34px;
    border-radius: 50%;
    background: var(--blue);
  }
  .brand__name {
    font-size: 30px;
    font-weight: 500;
    letter-spacing: 2px;
    color: var(--blue);
  }
  .details {
    position: absolute;
    left: 112px;
    top: 186px;
    color: var(--text);
  }
  .details__name {
    font-size: 28px;
    font-weight: 700;
    color: var(--blue);
    line-height: 1.1;
  }
  .details__title {
    font-size: 19px;
    font-weight: 700;
    color: var(--text);
    margin-bottom: 10px;
  }
  .details__line {
    font-size: 19px;
    line-height: 1.3;
  }
  .contact {
    list-style: none;
    margin-top: 6px;
  }
  .contact__item {
    display: flex;
    align-items: center;
    gap: 8px;
    font-size: 19px;
    line-height: 1.35;
  }
  .contact__icon { width: 16px; height: 16px; flex: none; }
  .card--arabic .details__name,
  .card--arabic .details__line--ar {
    font-family: "Tajawal", Arial, sans-serif;
  }
  .card--arabic .details__name { font-size: 34px; font-weight: 500; }
  .details__line--ar { text-align: left; }
</style>
</head>
<body>

  <section class="card card--arabic" lang="ar">
    <div class="card__decor" aria-hidden="true"></div>
    <div class="brand">
      <span class="brand__dot"></span>
      <span class="brand__name" lang="en">LUMEN SYSTEMS</span>
    </div>
    <div class="details">
      <p class="details__name" dir="rtl" style="text-align:left">سامر حداد</p>
      <p class="details__title" lang="en">Managing Director</p>
      <p class="details__line details__line--ar" dir="rtl">٤٢ طريق ميبل ريدج، فيرنون</p>
      <p class="details__line details__line--ar" dir="rtl">بي سي، كندا V2X 1K7</p>
      <ul class="contact" lang="en">
        <li class="contact__item">
          <svg class="contact__icon" viewBox="0 0 16 16"><path fill="#1a6fc0" d="M3 2l3 0 1 3-2 1.5a8 8 0 0 0 4.5 4.5L11 9l3 1v3c0 .6-.4 1-1 1A12 12 0 0 1 2 3c0-.6.4-1 1-1z"/></svg>
          555.214.0187
        </li>
        <li class="contact__item">
          <svg class="contact__icon" viewBox="0 0 16 16"><rect x="1" y="3" width="14" height="10" fill="#1a6fc0"/><path d="M1 3l7 6 7-6" fill="none" stroke="#fff" stroke-width="1.4"/></svg>
          samer@lumenmail.example
        </li>
        <li class="contact__item">
          <svg class="contact__icon" viewBox="0 0 16 16"><circle cx="8" cy="8" r="7" fill="#1a6fc0"/><path d="M1 8h14M8 1c-3 3-3 11 0 14M8 1c3 3 3 11 0 14" fill="none" stroke="#fff" stroke-width="1"/></svg>
          www.lumenweb.example
        </li>
      </ul>
    </div>
    <div class="card__band"><span class="card__band-blue"></span><span class="card__band-grey"></span></div>
  </section>

  <section class="card card--english" lang="en">
    <div class="card__decor" aria-hidden="true"></div>
    <div class="brand">
      <span class="brand__dot"></span>
      <span class="brand__name">LUMEN SYSTEMS</span>
    </div>
    <div class="details">
      <p class="details__name">SAMER HADDAD</p>
      <p class="details__title">Managing Director</p>
      <p class="details__line">42 Maple Ridge Rd, Vernon</p>
      <p class="details__line">B.C. Canada V2X 1K7</p>
      <ul class="contact">
        <li class="contact__item">
          <svg class="contact__icon" viewBox="0 0 16 16"><path fill="#1a6fc0" d="M3 2l3 0 1 3-2 1.5a8 8 0 0 0 4.5 4.5L11 9l3 1v3c0 .6-.4 1-1 1A12 12 0 0 1 2 3c0-.6.4-1 1-1z"/></svg>
          555.214.0187
        </li>
        <li class="contact__item">
          <svg class="contact__icon" viewBox="0 0 16 16"><rect x="1" y="3" width="14" height="10" fill="#1a6fc0"/><path d="M1 3l7 6 7-6" fill="none" stroke="#fff" stroke-width="1.4"/></svg>
          samer@lumenmail.example
        </li>
        <li class="contact__item">
          <svg class="contact__icon" viewBox="0 0 16 16"><circle cx="8" cy="8" r="7" fill="#1a6fc0"/><path d="M1 8h14M8 1c-3 3-3 11 0 14M8 1c3 3 3 11 0 14" fill="none" stroke="#fff" stroke-width="1"/></svg>
          www.lumenweb.example
        </li>
      </ul>
    </div>
    <div class="card__band"><span class="card__band-blue"></span><span class="card__band-grey"></span></div>
  </section>

</body>
</html>
```